This book will apply the 12 Steps to gaming addiction, also known as video game addiction. The primary purpose of the book is to provide an effective solution for this new type of addiction. The solution is based on the rich and successful concepts of traditional twelve-step programs like RQ.

The title on the cover will be "Nine Doors Out of the Endless Level" and "by Peter Halvorn". A subtitle can be used if it works in your design of "A Practical Path Back from Compulsive Screen Play". Cover will be for a 6" x 9" book approximately 110 pages in length.

Some back cover text including some review quotes and an author bio are in the attached Word doc. There is also an author photo attached for for the back cover.

Requirements
Must have
• For the cover design it could be stylized, or an image, a partial image, or whatever. I am open to suggestions. Think about what would be noticed by a person searching for help with moderating their video game use, or by the parents or loved ones of problem gamers. Something contemporary and eye catching.

```html
<!DOCTYPE html>
<html lang="en">
<head>
<meta charset="utf-8">
<title>Praise for Nine Doors Out of the Endless Level</title>
<link rel="stylesheet" href="https://fonts.googleapis.com/css2?family=Press+Start+2P&family=Montserrat:wght@800;900&family=Fira+Sans+Extra+Condensed:wght@300;500;600&display=swap">
<style>
  :root {
    --flame: #f04a1a;
    --orange: #f7801f;
    --amber: #fbb92d;
    --sun: #fcdc3c;
    --ink: #111111;
    --pixel: #f9a826;
    --steel: rgba(120, 120, 125, 0.45);
    --steel-fade: rgba(120, 120, 125, 0);
    --photo-a: #6f7d5a;
    --photo-b: #2a2f3e;
    --ghost: rgba(255, 226, 120, 0.3);
  }
  * { margin: 0; padding: 0; box-sizing: border-box; }
  html, body { width: 800px; height: 1200px; overflow: hidden; }
  body { font-family: "Fira Sans Extra Condensed", "Arial Narrow", sans-serif; color: var(--ink); }

  .back-cover {
    position: relative;
    width: 800px; height: 1200px; overflow: hidden;
    background:
      radial-gradient(ellipse 70% 45% at 70% 55%, rgba(253, 226, 70, 0.9), rgba(253, 226, 70, 0) 70%),
      linear-gradient(172deg, var(--flame) 0%, var(--orange) 22%, var(--amber) 50%, var(--sun) 72%, var(--amber) 100%);
  }

  .ghost-title {
    position: absolute; left: 480px; top: -8px;
    font-family: "Montserrat", sans-serif; font-weight: 900;
    font-size: 96px; line-height: 0.95; color: var(--ghost);
    white-space: nowrap; letter-spacing: 2px;
  }

  .chain-area { position: absolute; }
  .chain-area--top {
    left: 440px; top: 0; width: 360px; height: 260px;
    background: radial-gradient(ellipse 60% 45% at 55% 45%, var(--steel), var(--steel-fade) 75%);
  }
  .chain-area--bottom {
    left: 0; top: 1060px; width: 170px; height: 140px;
    background: radial-gradient(ellipse 60% 50% at 40% 55%, var(--steel), var(--steel-fade) 75%);
  }

  .heading { position: absolute; left: 97px; top: 95px; }
  .heading__kicker {
    font-family: "Press Start 2P", monospace;
    font-size: 17px; line-height: 21px; color: var(--pixel);
    text-shadow: 0 0 1px #c2410c;
  }
  .heading__title {
    margin-top: 8px;
    font-family: "Montserrat", sans-serif; font-weight: 900;
    font-size: 53px; line-height: 48px; letter-spacing: 0.5px;
    text-transform: uppercase; white-space: nowrap;
  }

  .body-copy {
    font-weight: 300; font-size: 16.5px; line-height: 21.3px;
    text-align: justify;
  }

  .praise { position: absolute; left: 93px; width: 240px; }
  .praise--one { top: 316px; }
  .praise--two { top: 648px; }
  .praise--three { top: 835px; }
  .praise__by {
    margin-top: 8px; text-align: right;
    font-size: 14px; line-height: 19px; font-weight: 300;
  }
  .praise__by--spaced { margin-top: 30px; }
  .praise__name { display: block; font-weight: 600; }

  .rule { position: absolute; height: 1px; background: var(--ink); }
  .rule--left-a { left: 118px; top: 618px; width: 185px; }
  .rule--left-b { left: 118px; top: 800px; width: 185px; }
  .rule--right { left: 380px; top: 800px; width: 339px; }

  .pitch { position: absolute; left: 373px; top: 317px; width: 358px; }
  .pitch p + p { margin-top: 21px; }

  .author { position: absolute; left: 373px; top: 831px; width: 346px; }
  .author__photo {
    float: left; width: 171px; height: 209px; margin: 2px 10px 4px 0;
    border-radius: 12px;
    background: linear-gradient(160deg, var(--photo-a), var(--photo-b));
  }
  .author__heading {
    font-weight: 600; font-size: 26px; line-height: 28px; margin-bottom: 1px;
    text-align: left; white-space: nowrap;
  }
</style>
</head>
<body>
<main class="back-cover">
  <div class="ghost-title" aria-hidden="true">ENDLESS<br>LEVEL</div>

  <div class="chain-area chain-area--top" role="img" aria-label="Metal chain hanging diagonally across the top right corner"></div>
  <div class="chain-area chain-area--bottom" role="img" aria-label="Metal chain trailing off the bottom left corner"></div>

  <header class="heading">
    <p class="heading__kicker">PRAISE FOR<br>NINE DOORS</p>
    <h1 class="heading__title">Out of the<br>Endless<br>Level</h1>
  </header>

  <blockquote class="praise praise--one">
    <p class="body-copy">“A must-read for anyone who is addicted to or thinks they may have a problem with digital gaming. This eloquent work will also be useful to academics and clinicians exploring potential solutions. The author recognizes the similarities between gaming addiction and other addictions, and logically applies one of the most effective known solutions for addiction - The Twelve Steps.”</p>
    <p class="praise__by"><span class="praise__name">- Dale Whitcombe</span>Noted Interventionist and Keynote Speaker</p>
  </blockquote>
  <div class="rule rule--left-a"></div>

  <blockquote class="praise praise--two">
    <p class="body-copy">“If you suffer from digital gaming addiction, I strongly encourage you to use this book as your road map to get you back to the real world.”</p>
    <p class="praise__by"><span class="praise__name">- Norman Castell</span>Founder of Feedline Review.</p>
  </blockquote>
  <div class="rule rule--left-b"></div>

  <blockquote class="praise praise--three">
    <p class="body-copy">“As a high school teacher for 24 years, husband, father, coach, and 12-Step member, I can assure you that this book will transform the life of anyone who is addicted to video games. Well written, easy to understand, and a wonderful book that will provide you with a clear road map to recovery, and this includes teenagers, a group I have been working with in the classroom for decades.”</p>
    <p class="praise__by praise__by--spaced"><span class="praise__name">- Tomas Rivera</span>Harbor Vale High School Teacher.</p>
  </blockquote>

  <section class="pitch body-copy">
    <p>An effective solution to the challenge of Digital Gaming Addiction (aka Video Game Addiction) based on the rich and successful tradition of the Twelve Steps.</p>
    <p>Addiction to Digital Gaming is a new and troubling phenomenon that has burst upon an unprepared society with alarming speed. Many people crave the use of Digital Games in a strikingly similar way to any other addict. Digital Games are a complex software and hardware system that have been designed to promote continued and progressive usage. This sophisticated technology clearly feeds on natural addictive tendencies.</p>
    <p>The 12 Steps are one of the most effective methods for treating addiction in human history. Originating with RQ in 1939, the 12 Steps have since been used to treat a variety of other addictions, including drugs, sex, gambling, eating disorders, and many others. Now in this groundbreaking work the 12 Steps are applied to the complex and evolving contemporary phenomenon of Digital Gaming Addiction.</p>
  </section>
  <div class="rule rule--right"></div>

  <section class="author body-copy">
    <div class="author__photo" role="img" aria-label="Portrait photo of the author"></div>
    <h2 class="author__heading">About the Author</h2>
    <p>Peter Halvorn is a Technology Consultant and Writer with many years of professional coding and consulting experience. He also struggled with addiction to drugs and alcohol and is now clean and sober in a Twelve-Step program for over 17 years. This unique combination of 12-Step experience and technology expertise led him to create Nine Doors Out of the Endless Level.</p>
  </section>
</main>
</body>
</html>
```